Criação de Layout de site para Computador & Internet
A empresa queria:
" Provedor de Internet banda larga para pessoas físicas e jurídicas com cobertura em duas cidades na região dos lagos, no Rio de Janeiro. "

```html
<!DOCTYPE html>
<html lang="pt-BR">
<head>
<meta charset="UTF-8">
<title>Velumar — Internet fibra ótica</title>
<link rel="stylesheet" href="https://fonts.googleapis.com/css2?family=Rubik:wght@400;500;700;800;900&display=swap">
<style>
  :root {
    --canvas: #ececec;
    --navy: #1a3580;
    --blue: #2248a3;
    --orange: #f7a21b;
    --ink: #1b2240;
    --white: #ffffff;
    --hero-dark: #1c120c;
    --hero-warm: #7a4a24;
    --hero-glow: #d89050;
  }
  * { box-sizing: border-box; margin: 0; padding: 0; }
  html, body {
    width: 1200px; height: 1200px; overflow: hidden;
    background: var(--canvas);
    font-family: "Rubik", sans-serif;
  }
  .site {
    position: absolute; left: 40px; top: 250px;
    width: 1120px; height: 700px;
    overflow: hidden;
    background: var(--blue);
    box-shadow: 0 20px 50px rgba(0,0,0,.18);
  }
  .topbar {
    height: 44px; background: var(--navy);
    display: flex; align-items: center; justify-content: flex-end;
    gap: 14px; padding-right: 120px;
  }
  .pill {
    height: 26px; border-radius: 13px;
    border: 1.5px solid rgba(255,255,255,.55);
    color: var(--white); font-size: 12px;
    display: flex; align-items: center; gap: 6px; padding: 0 14px;
  }
  .pill svg { width: 12px; height: 12px; }
  .pill--location { width: 170px; }
  .pill--search { width: 150px; }
  .pill--client {
    background: var(--orange); border-color: var(--orange);
    color: var(--ink); font-weight: 700; padding: 0 18px;
  }
  .header {
    height: 88px; background: var(--blue);
    display: flex; align-items: center; padding: 0 40px;
  }
  .brand {
    font-size: 36px; font-weight: 900; color: var(--orange);
    letter-spacing: -0.5px; margin-right: 40px;
    display: flex; align-items: center; gap: 8px;
  }
  .brand-dot { width: 14px; height: 14px; border-radius: 50%; background: var(--orange); }
  .nav { display: flex; align-items: center; gap: 14px; color: var(--white); font-size: 14px; font-weight: 500; }
  .nav .sep { opacity: .5; }
  .nav .is-active { color: var(--orange); }
  .social {
    margin-left: auto; display: flex; align-items: center; gap: 8px;
    color: var(--white); font-size: 13px; font-weight: 500;
  }
  .social-dot { width: 20px; height: 20px; border-radius: 50%; background: rgba(255,255,255,.75); }
  .segments {
    height: 30px; background: var(--orange);
    display: flex; align-items: center; padding-left: 40px; gap: 14px;
    font-size: 13px; font-weight: 500; color: var(--ink);
  }
  .segments .sep { opacity: .5; }
  .hero { position: relative; height: 538px; }
  .hero-photo {
    position: absolute; inset: 0;
    background:
      radial-gradient(ellipse 40% 55% at 55% 45%, var(--hero-glow) 0%, transparent 70%),
      radial-gradient(ellipse 30% 45% at 85% 35%, #a66a3a 0%, transparent 70%),
      linear-gradient(100deg, var(--hero-dark) 0%, #3a2414 40%, var(--hero-warm) 75%, #4a2e1a 100%);
  }
  .hero-copy { position: absolute; left: 60px; top: 80px; color: var(--white); }
  .hero-title { font-weight: 900; text-transform: uppercase; line-height: 1; }
  .hero-title .l1 { display: block; font-size: 70px; }
  .hero-title .l2 { display: block; font-size: 33px; font-weight: 700; margin-top: 4px; }
  .hero-title .l3 { display: block; font-size: 78px; margin-top: 18px; }
  .cta {
    display: inline-block; margin-top: 24px;
    background: var(--orange); color: var(--ink);
    font-size: 17px; font-weight: 700;
    padding: 11px 30px; border-radius: 24px;
  }
  .tagline { position: absolute; left: 60px; bottom: 66px; color: var(--white); }
  .tagline .t1 { font-size: 28px; font-weight: 500; }
  .tagline .t1 b { color: var(--orange); font-weight: 500; }
  .tagline .t2 { display: block; margin-top: 6px; font-size: 34px; font-weight: 500; }
  .tagline .mark { background: var(--orange); color: var(--ink); padding: 0 8px; font-weight: 800; }
</style>
</head>
<body>
  <main class="site">
    <div class="topbar">
      <span class="pill pill--location">
        <svg viewBox="0 0 12 12"><path d="M6 1a3.5 3.5 0 0 0-3.5 3.5C2.5 7 6 11 6 11s3.5-4 3.5-6.5A3.5 3.5 0 0 0 6 1zm0 5a1.5 1.5 0 1 1 0-3 1.5 1.5 0 0 1 0 3z" fill="#f7a21b"/></svg>
        Rio de Janeiro
      </span>
      <span class="pill pill--search">
        <svg viewBox="0 0 12 12"><circle cx="5" cy="5" r="3.5" fill="none" stroke="#fff" stroke-width="1.5"/><path d="M7.6 7.6 11 11" stroke="#fff" stroke-width="1.5"/></svg>
        Buscar no site
      </span>
      <span class="pill pill--client">Cliente</span>
    </div>

    <header class="header">
      <div class="brand">Velumar<span class="brand-dot"></span></div>
      <nav class="nav">
        <span class="is-active">Planos</span><span class="sep">|</span>
        <span>Viabilidade</span><span class="sep">|</span>
        <span>Vantagens</span><span class="sep">|</span>
        <span>Dicas</span><span class="sep">|</span>
        <span>Contato</span>
      </nav>
      <div class="social">
        Acesse nossas redes sociais
        <span class="social-dot"></span><span class="social-dot"></span>
      </div>
    </header>

    <div class="segments">
      <span>Pra você</span><span class="sep">|</span><span>Pra sua empresa</span>
    </div>

    <section class="hero">
      <div class="hero-photo" role="img" aria-label="Foto de família sorrindo à noite, criança usando notebook na sala com luz quente"></div>
      <div class="hero-copy">
        <h1 class="hero-title">
          <span class="l1">Conexão</span>
          <span class="l2">ideal para toda</span>
          <span class="l3">Família!</span>
        </h1>
        <span class="cta">Consulte disponibilidade!</span>
      </div>
      <p class="tagline">
        <span class="t1">internet <b>fibra ótica</b></span>
        <span class="t2">a <span class="mark">melhor internet</span> da região</span>
      </p>
    </section>
  </main>
</body>
</html>
```